Bramblewick Forage Business Cards

I need a business card with my logo, number, Facebook account, and some information about what I am selling. Green card with logo on the front. 555-214-8392 phone number, @bramblewickforage Facebook, •Orchardgrass Hay •Alfalfa Hay •Mixed Grass Hay , and “Premium Quality Hay” all written on the back.

Target Market(s)

Hay

Contact Information for Business Card

Phone number, Facebook, different types of hay.

Colors
00AB8E
00BBA5
67D7C9
C6EFE9
E9F9F6

```html
<!DOCTYPE html>
<html lang="en">
<head>
<meta charset="utf-8">
<title>Bramblewick Forage Business Cards</title>
<link rel="stylesheet" href="https://fonts.googleapis.com/css2?family=Open+Sans:wght@400;600&family=Arimo:wght@700&display=swap">
<style>
  :root {
    --page-bg: #c4c6c7;
    --card-green: #00963f;
    --card-white: #ffffff;
    --ink: #1b1b1b;
    --leaf-green: #1c9a45;
  }
  * { box-sizing: border-box; margin: 0; padding: 0; }
  html, body {
    width: 1187px;
    height: 1200px;
    overflow: hidden;
    background: var(--page-bg);
  }
  .canvas {
    position: relative;
    width: 1187px;
    height: 1200px;
  }
  .card {
    position: absolute;
    left: 216px;
    width: 756px;
    height: 432px;
    border-radius: 16px;
  }
  .card--front {
    top: 122px;
    background: var(--card-green);
  }
  .card--back {
    top: 644px;
    background: var(--card-white);
  }
  .brand {
    position: absolute;
    display: flex;
    align-items: center;
    gap: 16px;
    font-family: "Open Sans", sans-serif;
    font-weight: 600;
    color: var(--ink);
    white-space: nowrap;
  }
  .brand__mark {
    border-radius: 50%;
    flex: none;
  }
  .card--front .brand {
    left: 84px;
    top: 186px;
    font-size: 42px;
  }
  .card--front .brand__mark {
    width: 64px;
    height: 64px;
    background: #cfe6e4;
  }
  .card--back .brand {
    left: 162px;
    top: 150px;
    font-size: 36px;
  }
  .card--back .brand__mark {
    width: 56px;
    height: 56px;
    background: var(--leaf-green);
  }
  .contact {
    position: absolute;
    left: 330px;
    top: 222px;
    color: var(--ink);
  }
  .contact__phone {
    font-family: "Arimo", sans-serif;
    font-weight: 700;
    font-size: 41px;
    letter-spacing: 0.5px;
    line-height: 1;
  }
  .contact__social {
    display: flex;
    align-items: center;
    gap: 7px;
    margin-top: 16px;
    margin-left: 4px;
    font-family: "Open Sans", sans-serif;
    font-size: 22px;
    letter-spacing: 1px;
  }
  .contact__dot {
    width: 26px;
    height: 26px;
    border-radius: 50%;
    background: var(--leaf-green);
  }
  .products {
    position: absolute;
    left: 0;
    right: 0;
    top: 364px;
    display: flex;
    justify-content: center;
    gap: 10px;
    list-style: none;
    font-family: "Open Sans", sans-serif;
    font-size: 17px;
    letter-spacing: 0.4px;
    color: var(--ink);
  }
  .products__item {
    display: flex;
    align-items: center;
    gap: 5px;
  }
  .products__item::before {
    content: "";
    width: 7px;
    height: 7px;
    border-radius: 50%;
    background: var(--leaf-green);
  }
</style>
</head>
<body>
  <main class="canvas">
    <section class="card card--front" aria-label="Card front">
      <div class="brand">
        <span class="brand__mark"></span>
        <span class="brand__name">Bramblewick Forage</span>
      </div>
    </section>

    <section class="card card--back" aria-label="Card back">
      <div class="brand">
        <span class="brand__mark"></span>
        <span class="brand__name">Bramblewick Forage</span>
      </div>
      <div class="contact">
        <p class="contact__phone">555-214-8392</p>
        <p class="contact__social"><span class="contact__dot"></span>@bramblewickforage</p>
      </div>
      <ul class="products">
        <li class="products__item">Orchardgrass Hay</li>
        <li class="products__item">Alfalfa Hay</li>
        <li class="products__item">Mixed Grass Hay</li>
        <li class="products__item">Premium Quality Hay</li>
      </ul>
    </section>
  </main>
</body>
</html>
```